Vindgerdi - Start-up company selling electricity

Hello let me tell you about Vindgerdi.

Vindgerdi is start-up company selling electricity in Iceland. The operations of the company consist of making power usage forecasts for our customers, purchasing the electricity wholesale from the energy producers, and selling the electricity to the consumer. We are focused on tech by using optimization and machine learning to minimize electricity prices to our customers. Our marketing strategy is to portray a tech company mindset and to show dedication to driving down the electricity price on the market.

We need your help to make our website pop. Possible concepts to work with are as follows:

- Iceland the land of ice and fire
- Green energy
- Innovation
- Tech and data science

Link to our website: https://prufa.vindgerdi-example.is/
We are open to ideas.
Thank you!

Target Market(s)

Electricity consumers both homes and companies.

Number of Pages Required

1 page

Font styles to use
Serif
Sans Serif

```html
<!DOCTYPE html>
<html lang="en">
<head>
<meta charset="utf-8">
<title>Vindgerdi – Same electricity, just cheaper</title>
<link href="https://fonts.googleapis.com/css2?family=Poppins:wght@300;400;500;600&family=Exo+2:wght@600;700&family=Russo+One&family=Oswald:wght@500&display=swap" rel="stylesheet">
<style>
:root{
  --navy:#1c3461;
  --navy-deep:#15294e;
  --red:#a32a20;
  --red-soft:#b8392c;
  --ink:#222;
  --muted:#8a8a8a;
  --white:#fff;
  --paper:#f7f7f7;
  --slate:#7a8aa6;
  --rose:#c9776c;
}
*{margin:0;padding:0;box-sizing:border-box}
html,body{width:1200px;height:2745px;overflow:hidden}
body{position:relative;background:var(--white);font-family:"Poppins",sans-serif;color:var(--ink)}
.abs{position:absolute}
a{text-decoration:none}

/* header */
.site-header{left:0;top:0;width:1200px;height:82px;background:var(--white)}
.brand{display:flex;align-items:center;gap:10px;font-family:"Exo 2",sans-serif;font-weight:700;font-size:28px;color:var(--red);letter-spacing:.5px;white-space:nowrap}
.brand-dot{width:26px;height:26px;border-radius:50%;background:var(--navy)}
.site-header .brand{left:61px;top:24px}
.main-nav{left:556px;top:35px;display:flex;gap:30px;font-size:11px;color:#777;letter-spacing:.3px;text-transform:uppercase;white-space:nowrap}
.search-icon{left:983px;top:33px}
.phone-box{left:1035px;top:0;width:165px;height:82px;background:var(--red);display:flex;align-items:center;justify-content:center;gap:16px;color:var(--white);font-family:"Oswald",sans-serif;font-size:27px}

/* hero */
.hero{left:0;top:82px;width:1200px;height:638px;background:linear-gradient(160deg,#2a3f68 0%,#1f3663 50%,#1c3461 100%)}
.hero-photo{left:585px;top:82px;width:450px;height:638px;background:linear-gradient(180deg,#8fb6c4 0%,#b9c7b4 45%,#e8b566 72%,#b8902f 82%,#8a6a20 100%)}
.hero-title{left:61px;top:250px;font-family:"Russo One",sans-serif;font-weight:400;font-size:40px;line-height:56px;color:var(--white);letter-spacing:1px;white-space:nowrap}
.hero-title .accent{color:var(--red)}
.hero-text{left:61px;top:426px;width:460px;font-size:13px;line-height:22.5px;color:var(--white)}
.pill{display:flex;align-items:center;justify-content:space-between;border-radius:24px;font-size:13px;font-weight:500;letter-spacing:.4px;text-transform:uppercase;padding:0 5px 0 13px;white-space:nowrap}
.pill .pill-dot{width:34px;height:34px;border-radius:50%;background:var(--white);display:flex;align-items:center;justify-content:center;flex-shrink:0}
.pill .pill-dot i{width:14px;height:14px;border-radius:50%;background:var(--navy)}
.hero-cta{left:61px;top:498px;width:142px;height:43px;background:var(--red);color:var(--white)}

/* welcome */
.welcome-band{left:0;top:720px;width:1200px;height:102px;background:var(--paper)}
.bulb-photo{left:208px;top:789px;width:208px;height:304px;border-radius:48% 48% 30% 30%;background:radial-gradient(circle at 50% 30%,#f3b34a 0%,#c9c3b8 35%,#d9d6d0 60%,#f4f4f4 80%)}
.section-title{font-family:"Exo 2",sans-serif;font-weight:700;text-transform:uppercase;color:#111}
.welcome-title{left:481px;top:790px;font-size:30px}
.welcome-text{left:481px;top:848px;width:512px;font-size:11.5px;line-height:20.3px;color:var(--muted);font-weight:300}
.btn{display:flex;align-items:center;justify-content:center;border-radius:24px;color:var(--white);font-size:12.5px;font-weight:500;letter-spacing:.5px;text-transform:uppercase;width:119px;height:44px}
.btn-company{left:481px;top:998px;background:var(--navy)}
.btn-home{left:481px;top:1051px;background:var(--red)}

/* prices */
.prices{left:0;top:1178px;width:1200px;height:502px;background:linear-gradient(180deg,#2b2f38 0%,#262b36 45%,#1b2230 100%)}
.prices-title{left:0;top:1248px;width:1200px;text-align:center;font-family:"Exo 2",sans-serif;font-weight:600;font-size:30px;color:var(--white)}
.prices-sub{left:0;top:1310px;width:1200px;text-align:center;font-size:15px;color:var(--white)}
.price-card{top:1366px;width:286px;height:149px;border-radius:10px;color:var(--white);text-align:center}
.price-card .amount{display:block;margin-top:36px;font-size:38px;font-weight:600;line-height:46px}
.price-card .unit{display:block;margin-top:8px;font-size:15.5px}
.price-standard{left:300px;background:var(--red)}
.price-accel{left:615px;background:var(--navy)}
.compare-btn{left:529px;top:1561px;width:141px;height:43px;border:1.5px solid var(--white);color:var(--white)}

/* future */
.future-title{left:211px;top:1758px;font-size:30px;line-height:38px}
.future-text{left:211px;top:1850px;width:340px;font-size:11.5px;line-height:20.3px;color:var(--muted);font-weight:300}
.future-circle{left:727px;top:1763px;width:262px;height:262px;border-radius:50%;background:radial-gradient(circle at 50% 35%,#1f9e6a 0%,#0d4c6e 35%,#082a4e 75%)}
.future-frame{left:642px;top:1891px;width:136px;height:134px;background:var(--white);box-shadow:0 2px 8px rgba(0,0,0,.18);padding:8px}
.future-frame div{width:100%;height:100%;background:linear-gradient(180deg,#a8b9cc 0%,#c7d3de 50%,#4d6075 75%,#2f3b4d 100%)}
.future-illustration{left:136px;top:2025px;width:930px;height:240px}

/* footer */
.site-footer{left:0;top:2325px;width:1200px;height:420px;background:linear-gradient(180deg,#b43a2c 0%,#a8352a 100%)}
.footer-heading{top:2400px;font-family:"Exo 2",sans-serif;font-weight:600;font-size:15px;text-transform:uppercase;color:var(--white)}
.footer-list{top:2436px;list-style:none;font-size:11.5px;line-height:22.5px;color:var(--white)}
.footer-list li::before{content:"-  ";white-space:pre}
.contact-row{left:613px;display:flex;align-items:center;gap:18px;font-size:11.5px;color:var(--white)}
.contact-icon{width:33px;height:33px;border-radius:50%;background:var(--white);display:flex;align-items:center;justify-content:center}
.footer-blurb{left:889px;top:2436px;width:250px;font-size:11.5px;line-height:22.5px;color:var(--white)}
.newsletter{left:888px;top:2500px;width:251px;height:43px;border-radius:22px;background:rgba(255,255,255,.22);border:1px solid rgba(255,255,255,.35);display:flex;align-items:center;justify-content:space-between;padding:0 5px 0 13px;font-size:11.5px;color:var(--white)}
.newsletter .pill-dot{width:33px;height:33px;border-radius:50%;background:var(--white);display:flex;align-items:center;justify-content:center}
.newsletter .pill-dot i{width:14px;height:14px;border-radius:50%;background:var(--navy)}
.footer-rule{left:0;top:2625px;width:1200px;height:1px;background:rgba(255,255,255,.3)}
.footer-brand{left:0;top:2657px;width:1200px;display:flex;justify-content:center}
.footer-brand .brand{color:var(--white);font-size:26px}
.footer-brand .brand-dot{background:var(--white);width:22px;height:22px}
.copyright{left:0;top:2703px;width:1200px;text-align:center;font-size:9.5px;color:var(--white)}
</style>
</head>
<body>

<header class="abs site-header">
  <div class="abs brand"><span class="brand-dot"></span>VINDGERDI</div>
  <nav class="abs main-nav"><span>Terms of business</span><span>Question &amp; answer</span><span>About Vindgerdi</span></nav>
  <svg class="abs search-icon" width="16" height="16" viewBox="0 0 16 16" fill="none" stroke="#a32a20" stroke-width="1.6"><circle cx="6.5" cy="6.5" r="5"/><line x1="10.2" y1="10.2" x2="14.5" y2="14.5"/></svg>
</header>
<div class="abs phone-box">
  <svg width="32" height="32" viewBox="0 0 24 24" fill="#fff"><path d="M6.6 10.8a15.1 15.1 0 0 0 6.6 6.6l2.2-2.2c.3-.3.7-.4 1-.2 1.1.4 2.3.6 3.6.6.6 0 1 .4 1 1V20c0 .6-.4 1-1 1A17 17 0 0 1 3 4c0-.6.4-1 1-1h3.5c.6 0 1 .4 1 1 0 1.3.2 2.5.6 3.6.1.3 0 .7-.2 1z"/><path d="M14 3a7 7 0 0 1 7 7M14 6.5a3.5 3.5 0 0 1 3.5 3.5" stroke="#fff" stroke-width="1.6" fill="none"/></svg>
  <span>555-0199</span>
</div>

<section class="abs hero" role="img" aria-label="Snowy mountain landscape tinted in deep blue"></section>
<div class="abs hero-photo" role="img" aria-label="Photo of a power pylon and wind turbines over a wheat field at sunset"></div>
<h1 class="abs hero-title">SAME<br>ELECTRICITY<br><span class="accent">JUST CHEAPER!</span></h1>
<p class="abs hero-text">Lorem ipsum dolor sit amet, consectetur adipiscing elit, sed do eiusmod tempor incididunt ut labore et dolore magna aliqua.</p>
<a class="abs pill hero-cta">Contact us<span class="pill-dot"><i></i></span></a>

<div class="abs welcome-band"></div>
<div class="abs bulb-photo" role="img" aria-label="Photo of a glowing filament light bulb"></div>
<h2 class="abs section-title welcome-title">Welcome to business</h2>
<p class="abs welcome-text">Lorem ipsum dolor sit amet, consectetur adipiscing elit, sed do eiusmod tempor there to incididunt ut labore et dolore magna aliqua. Ut enim ad minim veniam, quis nostrud the exercitation ullamco laboris nisi ut aliquip ex ea commodo consequat. Duis aute irureh dolor in reprehenderit in voluptate velit esse cillum dolore eu fugiat nulla pariatur. the it Excepteur sint occaecat cupidatat non proident, sunt in culpa qui officia deserunt mollit anim id est laborum.</p>
<a class="abs btn btn-company">Company</a>
<a class="abs btn btn-home">Home</a>

<section class="abs prices" role="img" aria-label="Dark aerial photo of a city skyline at night"></section>
<h2 class="abs prices-title">PRICE LIST</h2>
<p class="abs prices-sub">Make a price comparison</p>
<div class="abs price-card price-standard"><span class="amount">6.95</span><span class="unit">ISK / kWh</span></div>
<div class="abs price-card price-accel"><span class="amount">6.22</span><span class="unit">ISK / kWh electric acceleration</span></div>
<a class="abs pill compare-btn">Verdvakt<span class="pill-dot"><i></i></span></a>

<h2 class="abs section-title future-title">The future is<br>exciting</h2>
<p class="abs future-text">Let's make the electricity system smarter together. Vindgerdi uses artificial intelligence, data science and automation to minimize costs and promote eccentricity</p>
<div class="abs future-circle" role="img" aria-label="Illustration of a glowing digital light bulb held above a hand"></div>
<div class="abs future-frame" role="img" aria-label="Photo of a technician installing solar panels near wind turbines"><div></div></div>
<svg class="abs future-illustration" role="img" aria-label="Illustration of a leaf, a globe, a green city skyline with wind turbines and a power plug" viewBox="0 0 930 240">
  <defs>
    <linearGradient id="lineTone" x1="0" x2="1" y1="0" y2="0">
      <stop offset="0" stop-color="#7a8aa6"/>
      <stop offset=".4" stop-color="#c9776c"/>
      <stop offset=".85" stop-color="#c9776c"/>
      <stop offset="1" stop-color="#7a8aa6"/>
    </linearGradient>
    <radialGradient id="globeTone" cx=".45" cy=".4" r=".6">
      <stop offset="0" stop-color="#f3f5f8"/>
      <stop offset="1" stop-color="#b9c3d3"/>
    </radialGradient>
    <linearGradient id="skyTone" x1="0" x2="0" y1="0" y2="1">
      <stop offset="0" stop-color="#c9776c" stop-opacity="0"/>
      <stop offset=".55" stop-color="#c9776c" stop-opacity=".55"/>
      <stop offset="1" stop-color="#c9776c" stop-opacity="0"/>
    </linearGradient>
  </defs>
  <line x1="60" y1="118" x2="850" y2="118" stroke="url(#lineTone)" stroke-width="3"/>
  <circle cx="257" cy="118" r="117" fill="#fff" stroke="#d3d9e3" stroke-width="3"/>
  <circle cx="257" cy="118" r="103" fill="url(#globeTone)"/>
  <rect x="400" y="40" width="390" height="150" fill="url(#skyTone)"/>
  <rect x="830" y="93" width="60" height="50" rx="10" fill="#7a8aa6"/>
</svg>

<footer class="abs site-footer" role="img" aria-label="Snowy village houses tinted in red"></footer>
<h3 class="abs footer-heading" style="left:61px">Vindgerdi ehf</h3>
<ul class="abs footer-list" style="left:61px"><li>ID number: 510312-0420</li><li>VAT number: 148203</li></ul>
<h3 class="abs footer-heading" style="left:338px">Links</h3>
<ul class="abs footer-list" style="left:338px"><li>Terms of business</li><li>Question &amp; Answer</li><li>About Vindgerdi</li></ul>
<h3 class="abs footer-heading" style="left:613px">Get in touch</h3>
<div class="abs contact-row" style="top:2438px"><span class="contact-icon"><svg width="14" height="16" viewBox="0 0 14 16" fill="none" stroke="#a32a20" stroke-width="1.6"><path d="M7 15s5-5 5-9a5 5 0 0 0-10 0c0 4 5 9 5 9z"/><circle cx="7" cy="6" r="1.8"/></svg></span>Sólvangur 7, 170 Nesbær</div>
<div class="abs contact-row" style="top:2482px"><span class="contact-icon"><svg width="14" height="14" viewBox="0 0 24 24" fill="#a32a20"><path d="M6.6 10.8a15.1 15.1 0 0 0 6.6 6.6l2.2-2.2c.3-.3.7-.4 1-.2 1.1.4 2.3.6 3.6.6.6 0 1 .4 1 1V20c0 .6-.4 1-1 1A17 17 0 0 1 3 4c0-.6.4-1 1-1h3.5c.6 0 1 .4 1 1 0 1.3.2 2.5.6 3.6.1.3 0 .7-.2 1z"/></svg></span>info@vindgerdi-example.is</div>
<div class="abs contact-row" style="top:2527px"><span class="contact-icon"><svg width="15" height="11" viewBox="0 0 15 11" fill="none" stroke="#a32a20" stroke-width="1.5"><rect x="1" y="1" width="13" height="9"/><path d="M1 1l6.5 5L14 1"/></svg></span>555-0199</div>
<h3 class="abs footer-heading" style="left:889px">Stay update</h3>
<p class="abs footer-blurb">Lorem ipsum dolor sit amet, consectetur adipiscing elit, sed do eiusmod.</p>
<div class="abs newsletter"><span>Enter Email...</span><span class="pill-dot"><i></i></span></div>
<div class="abs footer-rule"></div>
<div class="abs footer-brand"><div class="brand"><span class="brand-dot"></span>VINDGERDI</div></div>
<p class="abs copyright">Copyright © Vindgerdi 2020 - All rights reserved</p>

</body>
</html>
```